Food broker, trader, wholesaler, liquidator looking for a 5 pages website

Looking for a 5 pages website design. We are food brokers, traders, wholesaler and closeout buyer working with manufacturers, distributors, importers sell to retailers, food service operators and industrial (ingredients). We help market their products. We are a resource for those who need a solution in the distribution/selling/placement of food on the shelves, kitchens and pantries. Whether we open new accounts with new products or sell short dated inventory, we know where to go and get results.

Target Market(s)

Food manufacturers, food distributors, food brokers

Coding

Coded - Design and coding required

Number of Pages Required

4 page

Font styles to use
Serif

Requirements
Must have
• Food-food production-warehouse-Food packaging-people meeting-trucks-supermarket shelves-

```html
<!DOCTYPE html>
<html lang="en">
<head>
<meta charset="utf-8">
<title>Harbor Provisions — Food Brokers &amp; Traders</title>
<link href="https://fonts.googleapis.com/css2?family=Roboto+Slab:wght@400;500;700&family=Open+Sans:wght@400;600;700&display=swap" rel="stylesheet">
<style>
:root{
  --navy:#18165e;
  --navy-deep:#12104a;
  --accent:#5a5fd6;
  --ink:#222;
  --body:#444;
  --muted:#777;
  --gray-bg:#ebebeb;
  --line:#dcdcdc;
  --footer:#1c1e31;
  --white:#fff;
}
*{box-sizing:border-box;margin:0;padding:0}
html,body{width:1200px;height:5038px;overflow:hidden}
body{position:relative;background:var(--white);font-family:"Open Sans",sans-serif;color:var(--body)}
.abs{position:absolute}
section,header,footer{position:absolute;left:0;width:1200px}

/* header */
.site-header{top:0;height:110px;background:var(--white)}
.brand-mark{left:193px;top:8px;width:62px;height:62px;border-radius:50%;background:var(--navy)}
.brand-name{left:124px;top:80px;width:200px;text-align:center;font:700 11px "Roboto Slab",serif;color:var(--navy);letter-spacing:.2px}
.phone-badge{left:580px;top:18px;width:40px;height:40px;border-radius:50%;background:var(--navy)}
.phone-small{left:633px;top:16px;font-size:13px;color:var(--ink)}
.phone-number{left:633px;top:32px;font:500 20px "Roboto Slab",serif;color:var(--ink);letter-spacing:.5px}
.search{left:817px;top:22px;width:238px;height:34px;border:1px solid #cfcfcf;border-radius:17px;font-size:11px;color:#666;padding:9px 16px}
.search svg{position:absolute;right:12px;top:8px}
.main-nav{top:75px;left:522px;display:flex;gap:31px;font:700 13.5px "Roboto Slab",serif;color:var(--navy)}
.main-nav .active{color:var(--accent)}

/* hero */
.hero{top:110px;height:680px;background:radial-gradient(ellipse 520px 420px at 260px 300px,#2a27a0 0%,#201d86 50%,rgba(32,29,134,0) 100%),linear-gradient(100deg,#1b1866 0%,#221f7c 60%,#1b1866 100%);overflow:hidden}
.hero-photo{left:0;top:0}
.hero-mark{left:135px;top:104px;width:96px;height:96px;border-radius:50%;background:var(--white)}
.hero-title-1{left:135px;top:228px;font:700 42px "Roboto Slab",serif;color:var(--white);letter-spacing:.5px}
.hero-title-2{left:135px;top:268px;font:700 58px "Roboto Slab",serif;color:var(--white)}
.hero-text{left:135px;top:352px;width:290px;font:400 15.5px/24px "Roboto Slab",serif;color:var(--white)}
.btn{display:inline-block;font:700 13px "Roboto Slab",serif;text-align:center;border-radius:3px}
.btn-light{left:135px;top:473px;width:149px;height:45px;line-height:45px;background:var(--white);color:var(--navy)}
.slide-arrow{width:32px;height:32px;border-radius:50%;background:#111;top:302px}

/* welcome */
.welcome{top:790px;height:563px;background:var(--white)}
.welcome-photo{left:166px;top:101px;width:360px;height:360px;border-radius:50%;border:7px solid var(--navy);box-shadow:inset 0 0 0 8px var(--white);
  background:
   radial-gradient(ellipse 90px 150px at 38% 48%,#f4f6fa 0%,#e3e7ef 60%,rgba(227,231,239,0) 100%),
   radial-gradient(ellipse 120px 50px at 55% 82%,#b7723a 0%,#8f5326 55%,rgba(143,83,38,0) 100%),
   radial-gradient(ellipse 90px 140px at 78% 35%,#a9b3c4 0%,#7c879b 60%,rgba(124,135,155,0) 100%),
   linear-gradient(160deg,#dfe4ec 0%,#9aa5b8 55%,#5e6880 100%)}
.eyebrow{font:400 24px "Roboto Slab",serif;color:var(--ink)}
.section-title{font:700 38px "Roboto Slab",serif;color:var(--ink)}
.welcome .eyebrow{left:592px;top:96px}
.welcome .section-title{left:592px;top:126px}
.welcome-copy{left:592px;top:218px;width:450px;font-size:13.5px;line-height:22.5px;color:var(--body)}
.welcome-copy p+p{margin-top:14px}
.btn-dark{background:var(--navy);color:var(--white)}
.welcome .btn-dark{left:592px;top:412px;width:131px;height:39px;line-height:39px}

/* what we do */
.services{top:1353px;height:735px;background:var(--gray-bg)}
.center-title{left:0;width:1200px;text-align:center;font:700 36px "Roboto Slab",serif;color:var(--ink)}
.rule{height:3px;width:56px;background:var(--navy);left:572px}
.services .center-title{top:72px}
.services .rule{top:126px}
.card{top:172px;width:297px;height:442px;background:var(--white);overflow:hidden;box-shadow:0 0 0 1px #e2e2e2}
.card-icon{position:absolute;width:66px;height:66px;border-radius:50%;background:var(--navy)}
.card-icon svg{position:absolute;left:17px;top:17px}
.card-head{position:absolute;font:700 17px/24px "Roboto Slab",serif;color:var(--ink)}
.card-text{position:absolute;left:28px;width:241px;text-align:center;font-size:13px;line-height:21.5px;color:var(--body)}
.card-photo{position:absolute;left:0;width:297px;height:190px}
.card-feature{background:var(--navy)}
.card-feature .card-icon{background:var(--white)}
.card-feature .card-head,.card-feature .card-text{color:var(--white)}
.card-feature .mini-rule{position:absolute;left:114px;top:284px;width:60px;height:3px;background:var(--white)}

/* cycle */
.cycle{top:2088px;height:672px;background:var(--white)}
.cycle .eyebrow{left:143px;top:160px}
.cycle .section-title{left:143px;top:192px;font-size:33px}
.cycle .rule{left:143px;top:257px;width:66px}
.cycle-copy{left:143px;top:286px;width:326px;font-size:13.5px;line-height:22px;color:var(--body)}
.cycle .btn-dark{left:143px;top:466px;width:131px;height:39px;line-height:39px}
.cycle-diagram{left:0;top:0}
.cycle-diagram text{font-family:"Roboto Slab",serif}

/* testimonials */
.testimonials{top:2760px;height:503px;overflow:hidden;
  background:
   radial-gradient(ellipse 260px 160px at 120px 90px,rgba(70,80,160,.55),rgba(70,80,160,0)),
   radial-gradient(ellipse 300px 180px at 1080px 420px,rgba(90,70,150,.5),rgba(90,70,150,0)),
   radial-gradient(ellipse 240px 150px at 1050px 80px,rgba(60,90,140,.45),rgba(60,90,140,0)),
   radial-gradient(ellipse 260px 160px at 160px 430px,rgba(80,60,140,.45),rgba(80,60,140,0)),
   linear-gradient(160deg,#221f74 0%,#1a1862 50%,#231f78 100%)}
.testimonials .center-title{top:78px;color:var(--white);font-size:38px}
.testimonials .rule{top:140px;background:var(--white);width:60px;left:570px}
.quote{left:256px;top:178px;width:688px;text-align:center;font-size:17px;line-height:25.5px;color:var(--white)}
.avatar{border-radius:50%;border:2px solid var(--white);background:radial-gradient(circle at 50% 40%,#d8b79a 0%,#a98467 45%,#eceff4 75%,#b9c0cc 100%)}
.avatar-active{border:4px solid #e6b98a}
.tm-arrow{top:354px;color:var(--white);font-size:24px}
.tm-name{left:0;width:1134px;text-align:center;top:419px;font:700 11px "Open Sans",sans-serif;color:var(--white);letter-spacing:.5px}

/* news */
.news{top:3263px;height:735px;background:var(--gray-bg)}
.news .center-title{top:78px}
.news .rule{top:133px;width:60px;left:570px}
.news-card{background:var(--white);box-shadow:0 0 0 1px #e0e0e0;overflow:hidden}
.date-badge{position:absolute;width:78px;height:78px;border-radius:50%;background:var(--navy);color:var(--white);text-align:center;font:700 13px/15px "Roboto Slab",serif;padding-top:16px}
.news-title{position:absolute;font:700 16px/24px "Roboto Slab",serif;color:var(--ink);text-transform:uppercase;width:175px}
.news-text{position:absolute;font-size:12.8px;line-height:21px;color:var(--body)}
.news-photo{position:absolute}

/* partners */
.partners{top:3998px;height:479px;background:var(--white)}
.partners .center-title{top:78px}
.partner{width:174px;height:90px;border:1px solid var(--line);background:var(--white)}
.partner span{position:absolute;top:50%;left:50%;transform:translate(-50%,-50%);border-radius:3px;background:#9a9a9a}
.p-arrow{top:172px;font-size:44px;color:#b8b8b8;font-weight:300}

/* footer */
.site-footer{top:4477px;height:561px;background:transparent}
.footer-shape{left:0;top:0}
.footer-title{font:700 21px "Roboto Slab",serif;color:var(--white)}
.field{left:143px;width:359px;border:1px solid #c9c9d4;color:var(--white);font-size:11.5px;padding:10px 12px}
.submit{left:143px;top:340px;width:148px;height:38px;line-height:38px;background:#16137a;color:var(--white);font:700 14px "Roboto Slab",serif;text-align:center}
.contact-line{left:595px;font-size:13.5px;line-height:24px;color:#e6e6ee}
.contact-icon{left:563px}
.footer-mark{left:924px;top:104px;width:72px;height:72px;border-radius:50%;background:var(--white)}
.footer-brand{left:855px;top:186px;width:210px;text-align:center;font:700 12px "Roboto Slab",serif;color:var(--white)}
.footer-links{left:931px;top:233px;font-size:13px;line-height:27px;color:#e6e6ee}
.footer-rule{left:0;top:440px;width:1200px;height:1px;background:#3a3c52}
.copyright{left:143px;top:493px;font-size:13.5px;color:#e6e6ee}
.social{top:483px;width:38px;height:38px;border-radius:50%;border:2px solid var(--white)}
.social i{position:absolute;left:12px;top:12px;width:10px;height:10px;border-radius:50%;background:var(--white)}
</style>
</head>
<body>

<header class="site-header">
  <div class="abs brand-mark"></div>
  <div class="abs brand-name">HARBOR PROVISIONS</div>
  <div class="abs phone-badge">
    <svg width="40" height="40" viewBox="0 0 44 44"><path d="M15 13c2-1 3 0 4 2l1 3c0 1-1 2-2 3 1 3 3 5 6 6 1-1 2-2 3-2l3 1c2 1 3 2 2 4-1 2-3 3-5 3-8-1-14-7-15-15 0-2 1-4 3-5z" fill="#fff"/></svg>
  </div>
  <div class="abs phone-small">Contact Us Today!</div>
  <div class="abs phone-number">(555) 0142-7730</div>
  <div class="abs search">Search here
    <svg width="16" height="16" viewBox="0 0 16 16"><circle cx="7" cy="7" r="5" fill="none" stroke="#777" stroke-width="1.6"/><path d="M11 11l4 4" stroke="#777" stroke-width="1.6"/></svg>
  </div>
  <nav class="abs main-nav"><span class="active">HOME</span><span>ABOUT US</span><span>WHAT WE DO</span><span>CONTACT</span><span>GIVING BACK</span></nav>
</header>

<section class="hero">
  <svg class="abs hero-photo" width="1200" height="680" viewBox="0 0 1200 680" role="img" aria-label="Food factory worker in a white coat, hairnet and blue gloves sorting chocolate-dipped biscuits on a production line">
    <defs>
      <linearGradient id="heroBase" x1="0" y1="0" x2="1" y2="1">
        <stop offset="0" stop-color="#f1f3f7"/>
        <stop offset=".35" stop-color="#d6dae3"/>
        <stop offset=".6" stop-color="#c98a4a"/>
        <stop offset=".85" stop-color="#9a5a26"/>
        <stop offset="1" stop-color="#5e3317"/>
      </linearGradient>
      <radialGradient id="heroGreen" cx=".92" cy=".18" r=".35">
        <stop offset="0" stop-color="#5fb34a"/>
        <stop offset="1" stop-color="#5fb34a" stop-opacity="0"/>
      </radialGradient>
      <radialGradient id="heroBlue" cx=".55" cy=".5" r=".2">
        <stop offset="0" stop-color="#2a8fd8" stop-opacity=".8"/>
        <stop offset="1" stop-color="#2a8fd8" stop-opacity="0"/>
      </radialGradient>
      <radialGradient id="heroCoat" cx=".3" cy=".3" r=".4">
        <stop offset="0" stop-color="#ffffff"/>
        <stop offset="1" stop-color="#ffffff" stop-opacity="0"/>
      </radialGradient>
    </defs>
    <path d="M548 0 C425 180 418 470 548 680 L1200 680 L1200 0 Z" fill="#3330a0" opacity=".55"/>
    <g>
      <path d="M585 0 C470 180 462 470 590 680 L1200 680 L1200 0 Z" fill="url(#heroBase)"/>
      <path d="M585 0 C470 180 462 470 590 680 L1200 680 L1200 0 Z" fill="url(#heroCoat)"/>
      <path d="M585 0 C470 180 462 470 590 680 L1200 680 L1200 0 Z" fill="url(#heroGreen)"/>
      <path d="M585 0 C470 180 462 470 590 680 L1200 680 L1200 0 Z" fill="url(#heroBlue)"/>
    </g>
  </svg>
  <div class="abs hero-mark"></div>
  <div class="abs hero-title-1">HARBOR</div>
  <div class="abs hero-title-2">Provisions</div>
  <p class="abs hero-text">Harbor Provisions works with food manufacturers, brand owners, distributors and wholesalers market their products.</p>
  <a class="abs btn btn-light">LEARN MORE</a>
  <div class="abs slide-arrow" style="left:55px"><svg width="32" height="32"><path d="M18 10l-6 6 6 6" fill="none" stroke="#fff" stroke-width="2.5"/></svg></div>
  <div class="abs slide-arrow" style="left:1112px"><svg width="32" height="32"><path d="M14 10l6 6-6 6" fill="none" stroke="#fff" stroke-width="2.5"/></svg></div>
</section>

<section class="welcome">
  <div class="abs welcome-photo" role="img" aria-label="Food technician in protective clothing inspecting baked goods on a factory conveyor"></div>
  <div class="abs eyebrow">Welcome to</div>
  <h1 class="abs section-title">Harbor Provisions</h1>
  <div class="abs welcome-copy">
    <p>Harbor Provisions works with food manufacturers, brand owners, distributors and wholesalers market their products. Retail, Food Service and Industrial ingredients.</p>
    <p>Founded in 2008, Harbor Provisions started with the distribution of gluten free products understanding the need to provide access to unique flavors and products for the celiac consumers. From this, we expanded into deli, dairy, groceries, frozen and beverages.</p>
  </div>
  <a class="abs btn btn-dark">LEARN MORE</a>
</section>

<section class="services">
  <h2 class="abs center-title">What We Do</h2>
  <div class="abs rule"></div>

  <article class="abs card" style="left:129px">
    <div class="card-icon" style="left:18px;top:28px"><svg width="32" height="32" viewBox="0 0 32 32" fill="none" stroke="#fff" stroke-width="1.6"><circle cx="16" cy="9" r="5"/><path d="M6 29v-6a10 8 0 0 1 20 0v6zM12 22h8"/></svg></div>
    <div class="card-head" style="left:105px;top:33px">SALES &amp;<br>MARKETING</div>
    <p class="card-text" style="top:110px">We connect food buyers and sellers through a dedicated approach adscing elit, sed do eiusmod tempor incididunt ut labore et dolore magna aliqua. Ut enim ad minim veniam, quis nostrud</p>
    <div class="card-photo" style="top:252px;background:radial-gradient(ellipse 70px 90px at 55% 45%,#f2f2f2,rgba(242,242,242,0)),radial-gradient(ellipse 120px 50px at 40% 90%,#c8a98a,rgba(200,169,138,0)),linear-gradient(135deg,#cfd6df 0%,#8a96aa 50%,#4f586c 100%)" role="img" aria-label="Sales team meeting around a laptop in an office"></div>
  </article>

  <article class="abs card card-feature" style="left:452px">
    <div class="card-photo" style="top:0;background:radial-gradient(ellipse 50px 60px at 20% 35%,#2b3160,rgba(43,49,96,0)),radial-gradient(ellipse 90px 60px at 75% 35%,#6e8fc4,rgba(110,143,196,0)),radial-gradient(ellipse 70px 60px at 48% 65%,#e0c2a8,rgba(224,194,168,0)),linear-gradient(135deg,#eceef2 0%,#c7cedc 55%,#98a6bf 100%)" role="img" aria-label="Hands holding a smartphone beside a laptop showing charts and a coffee mug"></div>
    <div class="card-icon" style="left:26px;top:216px"><svg width="32" height="32" viewBox="0 0 32 32" fill="none" stroke="#18165e" stroke-width="1.6"><circle cx="9" cy="8" r="3"/><circle cx="23" cy="8" r="3"/><path d="M4 26v-9h10v9M18 26v-9h10v9M12 20h8"/></svg></div>
    <div class="card-head" style="left:114px;top:222px">MERCHANT<br>TRADING</div>
    <div class="mini-rule"></div>
    <p class="card-text" style="top:303px">We purchase goods anywhere and ship them Nationwide and Export adipiscing elit, sed do eiusmod tempor incididunt ut labore et dolore magna aliqua. Ut enim ad minim veniam, quis nostrud</p>
  </article>

  <article class="abs card" style="left:774px">
    <div class="card-icon" style="left:18px;top:28px"><svg width="32" height="32" viewBox="0 0 32 32" fill="none" stroke="#fff" stroke-width="1.6"><rect x="4" y="5" width="24" height="16" rx="2"/><path d="M10 27h12M16 21v6M10 15l4-4 3 3 5-5"/></svg></div>
    <div class="card-head" style="left:105px;top:33px">EXCESS<br>INVENTORY</div>
    <p class="card-text" style="top:110px">We buy closeouts and excess inventory for prisons, outlet stores &amp; discounters. adipiscing elit, sed do eiusmod tempor incididunt ut labore et dolore magna aliqua. Ut enim ad minim veniam, quis</p>
    <div class="card-photo" style="top:252px;background:radial-gradient(ellipse 80px 50px at 55% 35%,#d9a889,rgba(217,168,137,0)),radial-gradient(ellipse 140px 60px at 50% 90%,#5d4f45,rgba(93,79,69,0)),linear-gradient(135deg,#f2ece4 0%,#cdb59a 50%,#8a7158 100%)" role="img" aria-label="Two business people shaking hands over a desk with documents"></div>
  </article>
</section>

<section class="cycle">
  <svg class="abs cycle-diagram" width="1200" height="672" viewBox="0 2088 1200 672">
    <defs>
      <pattern id="gridFaint" width="14" height="14" patternUnits="userSpaceOnUse"><path d="M14 0H0V14" fill="none" stroke="#eceef6" stroke-width="1"/></pattern>
      <marker id="arrowHead" markerWidth="8" markerHeight="8" refX="6" refY="4" orient="auto"><path d="M0 0L8 4 0 8z" fill="#2a2870"/></marker>
    </defs>
    <circle cx="790" cy="2418" r="150" fill="url(#gridFaint)"/>
    <g fill="none" stroke="#2a2870" stroke-width="2" marker-end="url(#arrowHead)">
      <path d="M676 2258 Q708 2208 742 2204"/>
      <path d="M850 2200 Q900 2206 912 2244"/>
      <path d="M1000 2350 Q1010 2390 998 2414"/>
      <path d="M1030 2522 Q1000 2580 940 2596"/>
      <path d="M818 2648 Q800 2620 792 2632"/>
      <path d="M662 2652 Q620 2640 612 2532"/>
      <path d="M560 2420 Q566 2380 590 2352"/>
    </g>
    <g fill="#fff" stroke="#5a5fd6" stroke-width="3">
      <circle cx="792" cy="2229" r="64" stroke="#2a2870"/>
      <circle cx="948" cy="2307" r="64"/>
      <circle cx="987" cy="2479" r="64" stroke="#8b8fb0"/>
      <circle cx="880" cy="2604" r="64"/>
      <circle cx="706" cy="2600" r="64" stroke="#2a2870"/>
      <circle cx="598" cy="2473" r="64"/>
      <circle cx="635" cy="2303" r="64"/>
    </g>
    <g fill="none" stroke="#2a2870" stroke-width="2">
      <path d="M776 2217h32v22h-32zM780 2217v-8h8v8M796 2217v-10h8v10"/>
      <path d="M932 2286l16-10 16 10v18h-32zM940 2304v-10h16v10"/>
      <path d="M972 2458h30v22h-30zM972 2458l6-8h18l6 8M987 2450v30"/>
      <path d="M866 2575h28v16h-12l-6 6v-6h-10z"/>
      <path d="M694 2570h20v14h-20zM714 2575h9l5 5v4h-14z"/>
      <circle cx="700" cy="2588" r="3"/><circle cx="721" cy="2588" r="3"/>
      <path d="M584 2440h28v24h-28zM584 2448h28M584 2456h28"/>
      <path d="M622 2274h26l-3 18h-20zM626 2274l4-8h10l4 8"/>
    </g>
    <g font-size="14" font-weight="700" fill="#222" text-anchor="middle">
      <text x="792" y="2258">Food</text><text x="792" y="2274">Production</text>
      <text x="948" y="2332">Warehouse</text>
      <text x="987" y="2500">Food</text><text x="987" y="2516">Packaging</text>
      <text x="880" y="2618">People</text><text x="880" y="2634">Meeting</text>
      <text x="706" y="2618">Trucks</text>
      <text x="598" y="2488">Supermarket</text><text x="598" y="2504">Shelves</text>
      <text x="635" y="2320" font-size="16">Food</text>
    </g>
    <g fill="#18165e">
      <circle cx="700" cy="2235" r="14"/><circle cx="884" cy="2233" r="14"/><circle cx="999" cy="2379" r="14"/>
      <circle cx="954" cy="2557" r="14"/><circle cx="792" cy="2639" r="14"/><circle cx="620" cy="2563" r="14"/>
      <circle cx="581" cy="2381" r="14"/>
      <circle cx="790" cy="2405" r="42"/>
    </g>
    <g fill="#fff" font-size="13" font-weight="700" text-anchor="middle">
      <text x="700" y="2240">1</text><text x="884" y="2238">2</text><text x="999" y="2384">3</text>
      <text x="954" y="2562">4</text><text x="792" y="2644">5</text><text x="620" y="2568">6</text><text x="581" y="2386">7</text>
    </g>
    <text x="790" y="2468" font-size="12.5" font-weight="700" fill="#18165e" text-anchor="middle">HARBOR PROVISIONS</text>
  </svg>
  <div class="abs eyebrow">Our Cycle</div>
  <h2 class="abs section-title">Harbor Provisions</h2>
  <div class="abs rule"></div>
  <p class="abs cycle-copy">Lorem ipsum dolor sit amet, consectetur adipiscing elit, sed do eiusmod tempor incididunt ut labore et dolore magna aliqua. Ut enim ad minim veniam, quis nostrud exercitation ullamco laboris nisi ut aliquip ex ea commodo consequat. Duis aute irure dolor in reprehenderit in voluptate velit esse cillum dolore</p>
  <a class="abs btn btn-dark">LEARN MORE</a>
</section>

<section class="testimonials" role="img" aria-label="Dark blue tinted background of fresh produce">
  <h2 class="abs center-title">Testimonials</h2>
  <div class="abs rule"></div>
  <p class="abs quote"><b>&ldquo;</b> Lorem ipsum dolor sit amet, consectetur adipiscing elit, sed do eiusmod tempor incididunt ut labore et dolore magna aliqua. Ut enim ad minim veniam, quis nostrud exercitation ullamco laboris nisi ut aliquip ex ea commodo consequat. Duis aute irure dolor in reprehenderit in voluptate velit esse cillum dolore eu fugiat nulla pariatur. Excepteur sint occaecat cupidatat non proident <b>&rdquo;</b></p>
  <div class="abs tm-arrow" style="left:428px">&lsaquo;</div>
  <div class="abs avatar" style="left:470px;top:344px;width:56px;height:56px" role="img" aria-label="Client portrait"></div>
  <div class="abs avatar avatar-active" style="left:532px;top:337px;width:70px;height:70px" role="img" aria-label="Client portrait, John Doe"></div>
  <div class="abs avatar" style="left:609px;top:344px;width:56px;height:56px" role="img" aria-label="Client portrait"></div>
  <div class="abs avatar" style="left:678px;top:344px;width:56px;height:56px" role="img" aria-label="Client portrait"></div>
  <div class="abs tm-arrow" style="left:756px">&rsaquo;</div>
  <div class="abs tm-name">JOHN DOE</div>
</section>

<section class="news">
  <h2 class="abs center-title">Latest News</h2>
  <div class="abs rule"></div>

  <article class="abs news-card" style="left:145px;top:190px;width:297px;height:441px">
    <div class="date-badge" style="left:15px;top:21px">14<br>MARCH<br>2020</div>
    <div class="news-title" style="left:105px;top:24px">Duis aute irure dolor in reprehe nderit in volup</div>
    <p class="news-text" style="left:22px;top:114px;width:253px;text-align:center">Lorem ipsum dolor sit amet, coectetur adipiscing elit, sed do eiusmod tempor incididunt ut labore et dolore magna aliqua. Ut enim ad minim veniam, quis nostrud exercitation</p>
    <div class="news-photo" style="left:0;top:252px;width:297px;height:189px;background:radial-gradient(ellipse 60px 80px at 50% 40%,#f4f4f6,rgba(244,244,246,0)),radial-gradient(ellipse 80px 40px at 60% 70%,#3a7bc8,rgba(58,123,200,0)),linear-gradient(135deg,#e8dcc0 0%,#c6a56e 50%,#7a6340 100%)" role="img" aria-label="Warehouse worker packing food products into boxes"></div>
  </article>

  <article class="abs news-card" style="left:459px;top:190px;width:597px;height:209px">
    <div class="news-photo" style="left:0;top:0;width:280px;height:209px;background:radial-gradient(ellipse 90px 60px at 30% 15%,#2f6f57,rgba(47,111,87,0)),radial-gradient(ellipse 110px 50px at 55% 60%,#d46a86,rgba(212,106,134,0)),linear-gradient(160deg,#5f8c77 0%,#c9b8bf 45%,#e9e9ee 100%)" role="img" aria-label="Gloved hands handling trays of packaged fresh meat"></div>
    <div class="date-badge" style="left:310px;top:20px">14<br>MARCH<br>2020</div>
    <div class="news-title" style="left:403px;top:24px">Duis aute irure dolor in reprehe nderit in volup</div>
    <p class="news-text" style="left:317px;top:110px;width:262px">Lorem ipsum dolor sit amet, coectetur adipiscing elit, sed do eiusmod tempor incididunt ut labore et dolore magna aliqua. Ut enim ad minim veniam, quis</p>
  </article>

  <article class="abs news-card" style="left:459px;top:422px;width:597px;height:209px">
    <div class="news-photo" style="left:0;top:0;width:280px;height:209px;background:radial-gradient(ellipse 60px 90px at 35% 45%,#f3f5f9,rgba(243,245,249,0)),radial-gradient(ellipse 100px 40px at 60% 88%,#c77a35,rgba(199,122,53,0)),linear-gradient(135deg,#dfe3ea 0%,#a3adbe 55%,#6f7a90 100%)" role="img" aria-label="Food technicians in white coats checking baked goods on a production line"></div>
    <div class="date-badge" style="left:310px;top:20px">14<br>MARCH<br>2020</div>
    <div class="news-title" style="left:403px;top:24px">Duis aute irure dolor in reprehe nderit in volup</div>
    <p class="news-text" style="left:317px;top:110px;width:262px">Lorem ipsum dolor sit amet, coectetur adipiscing elit, sed do eiusmod tempor incididunt ut labore et dolore magna aliqua. Ut enim ad minim veniam, quis</p>
  </article>
</section>

<section class="partners">
  <h2 class="abs center-title">Our Partners</h2>
  <div class="abs p-arrow" style="left:88px">&lsaquo;</div>
  <div class="abs p-arrow" style="left:1090px">&rsaquo;</div>
  <div class="abs partner" style="left:143px;top:195px"><span style="width:104px;height:22px;background:#9aa0a8"></span></div>
  <div class="abs partner" style="left:328px;top:195px"><span style="width:92px;height:30px;background:#8e8e8e"></span></div>
  <div class="abs partner" style="left:514px;top:195px"><span style="width:98px;height:24px;background:#a8a8a8"></span></div>
  <div class="abs partner" style="left:700px;top:195px"><span style="width:74px;height:28px;background:#9a9a9a"></span></div>
  <div class="abs partner" style="left:886px;top:195px"><span style="width:110px;height:30px;background:#8a8a8a"></span></div>
  <div class="abs partner" style="left:143px;top:299px"><span style="width:136px;height:38px;background:#3a3a3a"></span></div>
  <div class="abs partner" style="left:328px;top:299px"><span style="width:104px;height:28px;background:#2e2e2e"></span></div>
  <div class="abs partner" style="left:514px;top:299px"><span style="width:112px;height:56px;background:#262626"></span></div>
  <div class="abs partner" style="left:700px;top:299px"><span style="width:120px;height:60px;border-radius:30px;background:#cfcfcf"></span></div>
  <div class="abs partner" style="left:886px;top:299px"><span style="width:132px;height:36px;background:#2a2a2a"></span></div>
</section>

<footer class="site-footer">
  <svg class="abs footer-shape" width="1200" height="561" viewBox="0 0 1200 561">
    <path d="M0 78 L600 0 L1200 78 Z" fill="#1f1d6c"/>
    <path d="M0 82 L600 8 L1200 82 V561 H0 Z" fill="#1c1e31"/>
  </svg>
  <div class="abs footer-title" style="left:143px;top:116px">Information request</div>
  <div class="abs field" style="top:174px;height:39px">Your Name</div>
  <div class="abs field" style="top:223px;height:38px">Email Address</div>
  <div class="abs field" style="top:272px;height:54px">Message</div>
  <div class="abs submit">SUBMIT</div>

  <div class="abs footer-title" style="left:563px;top:116px">Contact Us</div>
  <svg class="abs contact-icon" style="top:170px" width="16" height="20" viewBox="0 0 16 20"><path d="M8 1a6 6 0 0 0-6 6c0 5 6 12 6 12s6-7 6-12a6 6 0 0 0-6-6z" fill="none" stroke="#ccc" stroke-width="1.5"/><circle cx="8" cy="7" r="2" fill="#ccc"/></svg>
  <div class="abs contact-line" style="top:166px">Harbor Provisions<br>(c / o Quayside Business Park)<br>20400 Lakemoor (LM), Italy</div>
  <svg class="abs contact-icon" style="top:253px" width="16" height="16" viewBox="0 0 16 16"><path d="M3 1c1 0 2 1 2 2l1 2-1 2c1 2 2 3 4 4l2-1 2 1c1 0 2 1 2 2l-1 2C7 15 1 9 1 3z" fill="none" stroke="#ccc" stroke-width="1.3"/></svg>
  <div class="abs contact-line" style="top:249px">Phone: +39/010/5550123</div>
  <svg class="abs contact-icon" style="top:283px" width="16" height="16" viewBox="0 0 16 16"><rect x="1" y="5" width="14" height="9" fill="#ccc"/><rect x="4" y="1" width="8" height="5" fill="none" stroke="#ccc" stroke-width="1.3"/></svg>
  <div class="abs contact-line" style="top:279px">Fax: 555 0199 4400</div>
  <svg class="abs contact-icon" style="top:320px" width="16" height="14" viewBox="0 0 16 14"><rect x="1" y="1" width="14" height="12" fill="none" stroke="#ccc" stroke-width="1.3"/><path d="M1 1l7 6 7-6" fill="none" stroke="#ccc" stroke-width="1.3"/></svg>
  <div class="abs contact-line" style="top:316px">Email: hello@harborprovisions.com</div>

  <div class="abs footer-mark"></div>
  <div class="abs footer-brand">HARBOR PROVISIONS</div>
  <div class="abs footer-links">About US<br>What we do<br>Contact<br>Giving Back</div>

  <div class="abs footer-rule"></div>
  <div class="abs copyright">(c) 2020 Harbor Provisions | All Rights Reserved</div>
  <div class="abs social" style="left:921px"><i></i></div>
  <div class="abs social" style="left:970px"><i></i></div>
  <div class="abs social" style="left:1019px"><i></i></div>
</footer>

</body>
</html>
```